Amber Lantern Cafe Business Card

We need a business card design for a new European Cafe. Main menu will be coffee and deserts.

Industry/Entity Type

Business

Requirements
Must have
• Logo - 1 of the attached versions
Address - TBA (you can use 48 Mossy Rd Unit 3 for now)
Phone - TBA (you can use 555-203-8841 for now)

```html
<!DOCTYPE html>
<html lang="en">
<head>
<meta charset="utf-8">
<title>Amber Lantern Cafe – Business Card</title>
<link href="https://fonts.googleapis.com/css2?family=Carlito:wght@400;700&display=swap" rel="stylesheet">
<style>
  :root {
    --card-bg: #ffffff;
    --ink: #111111;
    --brand-dark: #231f20;
    --accent-red: #a4262c;
  }
  html, body {
    margin: 0;
    padding: 0;
    width: 1200px;
    height: 693px;
    overflow: hidden;
    background: var(--card-bg);
  }
  .card {
    position: relative;
    width: 1200px;
    height: 693px;
    background: var(--card-bg);
    font-family: "Carlito", "Calibri", sans-serif;
    color: var(--ink);
  }
  .brand-square {
    position: absolute;
    left: 43px;
    top: 40px;
    width: 283px;
    height: 280px;
    border-radius: 12px;
    background: var(--brand-dark);
  }
  .brand-name {
    position: absolute;
    left: 370px;
    top: 72px;
    width: 790px;
    text-align: center;
    font-weight: 400;
    color: var(--brand-dark);
    line-height: 1;
    margin: 0;
  }
  .brand-name .line-main {
    display: block;
    font-size: 104px;
    letter-spacing: -1px;
  }
  .brand-name .line-sub {
    display: block;
    font-size: 74px;
    margin-top: 14px;
    letter-spacing: 3px;
  }
  .contact {
    position: absolute;
    left: 468px;
    top: 382px;
    width: 600px;
    text-align: center;
    font-weight: 700;
    font-size: 47px;
    line-height: 71px;
  }
  .contact p { margin: 0; }
  .contact .person,
  .contact .role { color: var(--accent-red); }
  .contact .address,
  .contact .phone { color: var(--ink); }
</style>
</head>
<body>
  <div class="card">
    <div class="brand-square"></div>
    <h1 class="brand-name">
      <span class="line-main">Amber Lantern</span>
      <span class="line-sub">Cafe</span>
    </h1>
    <div class="contact">
      <p class="person">Daniel Hart</p>
      <p class="role">Manager</p>
      <p class="address">48 Mossy Rd Unit 3</p>
      <p class="phone">555-203-8841</p>
    </div>
  </div>
</body>
</html>
```